Business Card Design for a Personal Trainer

I need a business card design for my job as a personal trainer. It should have a unique, modern and exclusive design. On the front there should be only my logo with my name and my job. 0162/3819204 Tobias Lendhart Wiesengrundweg 14 80417 Munich Germany The most important contact information is the web adress. it can be bigger than the rest, but its not necessary. The card should be 8,5cmx5,5cm big. Font: Roboto. Colors: black, white, gray, 56c1ff.

```html
<!DOCTYPE html>
<html lang="de">
<head>
<meta charset="utf-8">
<title>Tobias Lendhart – Personal Trainer Visitenkarte</title>
<link rel="stylesheet" href="https://fonts.googleapis.com/css2?family=Roboto:wght@300;400&display=swap">
<style>
  :root {
    --page-bg: #d8d5d1;
    --card-dark: #0e0e0f;
    --card-mid: #1d1d1f;
    --photo-light: #5a5a5c;
    --photo-dark: #161617;
    --text-light: #dcdcdc;
    --text-muted: #b4b4b4;
    --rule: #8c8c8c;
    --accent: #56c1ff;
  }
  * { margin: 0; padding: 0; box-sizing: border-box; }
  html, body {
    width: 1200px;
    height: 970px;
    overflow: hidden;
    background: var(--page-bg);
    font-family: "Roboto", sans-serif;
  }
  .canvas {
    position: relative;
    width: 1200px;
    height: 970px;
  }
  .business-card {
    position: absolute;
    left: 100px;
    top: 208px;
    width: 1000px;
    height: 554px;
    background: linear-gradient(115deg, var(--card-mid) 0%, var(--card-dark) 55%, #19191a 100%);
    overflow: hidden;
    color: var(--text-light);
  }
  .trainer-photo {
    position: absolute;
    left: 0;
    top: 0;
    width: 500px;
    height: 554px;
    background:
      radial-gradient(ellipse 42% 48% at 50% 58%, var(--photo-light) 0%, #3a3a3c 45%, transparent 80%),
      linear-gradient(90deg, #262628 0%, var(--photo-dark) 100%);
  }
  .brand-lockup {
    position: absolute;
    left: 500px;
    top: 120px;
    width: 448px;
    text-align: center;
  }
  .brand-name {
    display: inline-flex;
    align-items: center;
    gap: 14px;
    font-weight: 300;
    font-size: 32px;
    letter-spacing: 1px;
    color: var(--text-light);
  }
  .brand-square {
    width: 16px;
    height: 16px;
    background: var(--text-muted);
  }
  .brand-tagline {
    display: flex;
    align-items: center;
    justify-content: center;
    gap: 10px;
    margin-top: 6px;
    font-weight: 300;
    font-size: 13px;
    letter-spacing: 4px;
    color: var(--text-muted);
  }
  .brand-tagline::before,
  .brand-tagline::after {
    content: "";
    width: 56px;
    height: 1px;
    background: var(--rule);
  }
  .contact-name {
    position: absolute;
    left: 555px;
    top: 246px;
    font-weight: 400;
    font-size: 29px;
    color: var(--text-light);
  }
  .contact-list {
    position: absolute;
    left: 555px;
    top: 302px;
    list-style: none;
    font-weight: 300;
    font-size: 21px;
    line-height: 34px;
    color: var(--text-muted);
  }
  .contact-item {
    display: flex;
    align-items: flex-start;
  }
  .contact-icon {
    width: 18px;
    height: 18px;
    margin: 8px 14px 0 0;
    fill: var(--text-light);
    flex: none;
  }
  .contact-website {
    position: absolute;
    left: 489px;
    top: 468px;
    font-weight: 300;
    font-size: 31px;
    color: var(--text-light);
  }
</style>
</head>
<body>
<main class="canvas">
  <section class="business-card">
    <div class="trainer-photo" role="img" aria-label="Black-and-white portrait of the trainer with arms crossed, gym equipment in the background"></div>

    <div class="brand-lockup">
      <div class="brand-name"><span class="brand-square"></span>TOBIAS LENDHART</div>
      <div class="brand-tagline">PERSONAL TRAINER</div>
    </div>

    <h1 class="contact-name">Tobias Lendhart</h1>

    <ul class="contact-list">
      <li class="contact-item">
        <svg class="contact-icon" viewBox="0 0 18 18" aria-hidden="true">
          <path d="M1 6c0-2 3-4 8-4s8 2 8 4v1h-4V5H5v2H1z"/>
          <path d="M3 9h12l1 7H2z"/>
        </svg>
        <span>0162/3819204</span>
      </li>
      <li class="contact-item">
        <svg class="contact-icon" viewBox="0 0 18 18" aria-hidden="true">
          <path d="M1 7l8-5 8 5v9H1z"/>
          <path d="M3 8l6 4 6-4" fill="none" stroke="#0e0e0f" stroke-width="1.5"/>
        </svg>
        <span>t.lendhart@mailpost.de</span>
      </li>
      <li class="contact-item">
        <svg class="contact-icon" viewBox="0 0 18 18" aria-hidden="true">
          <path d="M9 1l8 8h-2.5v8H11v-5H7v5H3.5V9H1z"/>
        </svg>
        <span>Wiesengrundweg 14<br>80417 München</span>
      </li>
    </ul>

    <p class="contact-website">www.tobiaslendhart.de</p>
  </section>
</main>
</body>
</html>
```